Marlow Vale Stud website

We would like to create a horse stud/agistment farm website similar to this websites we have attached below:
www.thornbeck.com.au
www.quillstead.com.au
www.brackley.com
www.pimsey.com.au
The main colour scheme are purple and white to align with the stable's racing colours.
We have also attach the company logo and also images of the farm and create some ideas for the website.
Many thanks for looking into this project!

```html
<!DOCTYPE html>
<html lang="en">
<head>
<meta charset="utf-8">
<title>Marlow Vale Stud</title>
<link href="https://fonts.googleapis.com/css2?family=Lato:wght@400;700;900&display=swap" rel="stylesheet">
<style>
:root{
  --purple:#2e1537;
  --purple-deep:#1f0d28;
  --ink:#1a1a1a;
  --text:#444;
  --white:#fff;
  --light:#efefef;
  --footer:#1c1c1c;
}
*{box-sizing:border-box;margin:0;padding:0}
html,body{width:1200px;height:4176px;overflow:hidden}
body{font-family:'Lato',sans-serif;color:var(--ink);background:var(--white);position:relative}
section,header,footer{position:relative;width:1200px;overflow:hidden}
.abs{position:absolute}
.section-title{position:absolute;left:0;width:100%;text-align:center;font-weight:900;font-size:40px;letter-spacing:1px;text-transform:uppercase}

/* header */
.site-header{height:112px;background:var(--white)}
.brand{position:absolute;left:75px;top:30px;display:flex;align-items:center;gap:14px}
.brand-dot{width:44px;height:44px;border-radius:50%;background:var(--purple)}
.brand-name{font-weight:700;font-size:30px;color:var(--purple);text-transform:uppercase;letter-spacing:.5px}
.main-nav{position:absolute;right:73px;top:46px;display:flex;gap:28px;font-size:14px;font-weight:700;text-transform:uppercase;color:var(--ink)}

/* hero */
.hero{height:548px}
.hero-photo{position:absolute;inset:0;background:linear-gradient(180deg,#9bb0c0 0%,#c9cfc4 20%,#5d7a3a 45%,#6d9a35 70%,#4f7a27 100%)}
.hero-title{position:absolute;top:200px;width:100%;text-align:center;color:var(--white);font-weight:900;font-size:76px;letter-spacing:1px;text-shadow:0 2px 8px rgba(0,0,0,.35)}
.hero-sub{position:absolute;top:290px;width:100%;text-align:center;color:var(--white);font-weight:700;font-size:30px;text-shadow:0 2px 6px rgba(0,0,0,.35)}
.hero-arrow{position:absolute;top:210px}
.hero-down{position:absolute;left:578px;top:470px}

/* welcome */
.welcome{height:370px}
.welcome .section-title{top:56px}
.welcome-text{position:absolute;top:118px;left:85px;width:1030px;text-align:center;font-size:15px;line-height:29px;color:var(--text)}
.btn{position:absolute;display:flex;align-items:center;justify-content:center;background:var(--purple);color:var(--white);font-weight:700;font-size:15px;text-transform:uppercase;letter-spacing:.5px}
.welcome .btn{left:510px;top:245px;width:180px;height:58px}

/* stallions */
.stallions{height:543px}
.stallions-bg{position:absolute;inset:0;background:linear-gradient(180deg,#2a1236 0%,#3a1c44 40%,#24122a 75%,#1a0e1c 100%)}
.stallions .section-title{top:58px;color:var(--white)}
.card{position:absolute;top:145px;width:332px}
.card-photo{height:198px}
.card-name{margin-top:30px;text-align:center;color:var(--white);font-weight:700;font-size:22px}
.card-text{margin-top:12px;text-align:center;color:#ddd;font-size:13px;line-height:18px;padding:0 30px}
.slider-arrow{position:absolute}

/* gallery */
.gallery{height:682px}
.gallery .section-title{top:50px}
.gallery-item{position:absolute;width:332px;height:218px}

/* video */
.video{height:599px;background:var(--light)}
.video .section-title{top:50px}
.video-frame{position:absolute;left:164px;top:142px;width:872px;height:381px;background:linear-gradient(180deg,#4d6da0 0%,#7f95b8 45%,#3b3430 75%,#2a211c 100%)}
.play{position:absolute;left:406px;top:161px}

/* news */
.news{height:506px}
.news .section-title{top:58px}
.news-photo{position:absolute;left:136px;top:147px;width:451px;height:290px;background:linear-gradient(180deg,#3a4a3a 0%,#6b7a52 45%,#5f8a3a 70%,#c0504a 88%,#b98a3a 100%)}
.date-badge{position:absolute;left:78px;top:161px;width:117px;height:103px;background:var(--purple);color:var(--white);text-align:center;font-weight:900}
.date-badge .m{font-size:16px;padding-top:8px;line-height:18px}
.date-badge .d{font-size:42px;line-height:42px}
.date-badge .y{font-size:17px;line-height:20px}
.news-body{position:absolute;left:615px;top:152px;width:480px}
.news-head{font-weight:900;font-size:19px;line-height:24px;color:var(--purple);text-transform:uppercase}
.news-text{margin-top:12px;font-size:14px;line-height:25px;color:var(--text)}
.news .btn{left:615px;top:378px;width:178px;height:61px}

/* get in touch */
.touch{height:281px}
.map{position:absolute;inset:0;background:linear-gradient(135deg,#e4e4e2 0%,#d6d8d4 50%,#e8e8e6 100%)}
.touch-box{position:absolute;left:370px;top:47px;width:457px;height:190px;background:var(--white);box-shadow:0 4px 14px rgba(0,0,0,.25);text-align:center}
.touch-title{margin-top:26px;font-weight:900;font-size:30px;text-transform:uppercase}
.touch-phone{margin-top:8px;display:flex;justify-content:center;align-items:center;gap:16px;font-weight:700;font-size:42px;color:var(--purple)}
.touch-mail{margin-top:8px;font-size:20px;color:var(--ink)}

/* contact */
.contact{height:465px}
.contact-bg{position:absolute;inset:0;background:linear-gradient(180deg,#1b2416 0%,#202c1c 40%,#2e2a22 80%,#1c1a16 100%)}
.contact .section-title{top:52px;color:var(--white)}
.contact-sub{position:absolute;top:108px;width:100%;text-align:center;color:var(--white);font-size:30px}
.field{position:absolute;border:1px solid rgba(255,255,255,.75);color:var(--white);font-size:13px;padding:12px 14px}
.send{position:absolute;left:476px;top:365px;width:248px;height:56px;background:var(--purple-deep);color:var(--white);font-weight:700;font-size:16px;display:flex;align-items:center;justify-content:center;text-transform:uppercase}

/* footer */
.site-footer{height:70px;background:var(--footer)}
.copyright{position:absolute;left:75px;top:28px;font-size:11px;color:#888}
.social{position:absolute;right:136px;top:14px;display:flex;gap:10px}
.social span{width:40px;height:40px;border:1.5px solid #777;border-radius:50%}
</style>
</head>
<body>

<header class="site-header">
  <div class="brand"><span class="brand-dot"></span><span class="brand-name">Marlow Vale Stud</span></div>
  <nav class="main-nav"><span>Home</span><span>About Us</span><span>Stallions</span><span>Sales</span><span>Gallery</span><span>News</span><span>Contact Us</span></nav>
</header>

<section class="hero">
  <div class="hero-photo" role="img" aria-label="Horse grazing in a green paddock beneath trees and a cloudy sky"></div>
  <h1 class="hero-title">MARLOW VALE STUD</h1>
  <p class="hero-sub">Class aptent taciti sociosqu...</p>
  <svg class="hero-arrow" style="left:70px" width="30" height="100" viewBox="0 0 30 100"><polyline points="28,2 2,50 28,98" fill="none" stroke="#fff" stroke-width="2"/></svg>
  <svg class="hero-arrow" style="left:1100px" width="30" height="100" viewBox="0 0 30 100"><polyline points="2,2 28,50 2,98" fill="none" stroke="#fff" stroke-width="2"/></svg>
  <svg class="hero-down" width="44" height="44" viewBox="0 0 44 44"><circle cx="22" cy="22" r="20" fill="none" stroke="#fff" stroke-width="2"/><polyline points="13,18 22,27 31,18" fill="none" stroke="#fff" stroke-width="2.5"/></svg>
</section>

<section class="welcome">
  <h2 class="section-title">Welcome to our website</h2>
  <p class="welcome-text">Vivamus egestas risus in magna varius commodo. Sed semper viverra egestas. Etiam pretium porttitor lectus, vel ornare neque porta volutpat.<br>Quisque aliquet neque eu luctus condimentum. Suspendisse placerat tellus at sagittis vestibulum. Integer eget semper lectus, non ultricies mn ulla facilisi.<br>In sed arcu vel odio tempus pellentesque. Aenean gravida dapibus ligula. Nulla sit amet nibh augue.</p>
  <a class="btn">Read More</a>
</section>

<section class="stallions">
  <div class="stallions-bg" role="img" aria-label="Dusky paddock at sunset in deep purple tones"></div>
  <h2 class="section-title">Stallions</h2>
  <div class="card" style="left:75px">
    <div class="card-photo" role="img" aria-label="Pale grey stallion standing in a paddock" style="background:linear-gradient(180deg,#a9b7c4 0%,#d9d2c0 45%,#5f8a33 70%,#4b7a28 100%)"></div>
    <h3 class="card-name">Curabitur</h3>
    <p class="card-text">Vivamus egestas risus in magna varius commodo semper viverra egestaetiam pretium porttitor lectus</p>
  </div>
  <div class="card" style="left:434px">
    <div class="card-photo" role="img" aria-label="Chestnut stallion standing on a gravel lane" style="background:linear-gradient(180deg,#6f8a5a 0%,#8c5a32 45%,#a06534 65%,#8f8a82 100%)"></div>
    <h3 class="card-name">Curabitur</h3>
    <p class="card-text">Vivamus egestas risus in magna varius commodo semper viverra egestaetiam pretium porttitor lectus</p>
  </div>
  <div class="card" style="left:793px">
    <div class="card-photo" role="img" aria-label="Close view of a pale stallion by a fence" style="background:linear-gradient(90deg,#6f8a4a 0%,#c9b9a0 45%,#e2d9c8 70%,#8aa45a 100%)"></div>
    <h3 class="card-name">Curabitur</h3>
    <p class="card-text">Vivamus egestas risus in magna varius commodo semper viverra egestaetiam pretium porttitor lectus</p>
  </div>
  <svg class="slider-arrow" style="left:42px;top:340px" width="16" height="26" viewBox="0 0 16 26"><polyline points="13,2 3,13 13,24" fill="none" stroke="#fff" stroke-width="4"/></svg>
  <svg class="slider-arrow" style="left:1140px;top:340px" width="16" height="26" viewBox="0 0 16 26"><polyline points="3,2 13,13 3,24" fill="none" stroke="#fff" stroke-width="4"/></svg>
</section>

<section class="gallery">
  <h2 class="section-title">Gallery</h2>
  <div class="gallery-item" role="img" aria-label="Paddock fence under a dramatic evening sky" style="left:75px;top:147px;background:linear-gradient(180deg,#5a6f8a 0%,#c9a77a 40%,#5f6a3a 70%,#4a3a2a 100%)"></div>
  <div class="gallery-item" role="img" aria-label="Horses grazing beneath tall gum trees" style="left:434px;top:147px;background:linear-gradient(180deg,#3f4a32 0%,#5a6f3a 45%,#6f9a3a 75%,#5a8a2f 100%)"></div>
  <div class="gallery-item" role="img" aria-label="Open green paddock under a blue sky" style="left:793px;top:147px;background:linear-gradient(180deg,#5d86c8 0%,#a9c3e2 40%,#5e8f34 60%,#3f7a24 100%)"></div>
  <div class="gallery-item" role="img" aria-label="Aerial view of stables and yards" style="left:75px;top:390px;background:linear-gradient(180deg,#3f7a2f 0%,#5f9a3f 50%,#8a9a6a 75%,#4f7a2a 100%)"></div>
  <div class="gallery-item" role="img" aria-label="Aerial view of farm buildings and hills" style="left:434px;top:390px;background:linear-gradient(180deg,#6f9ad2 0%,#9ab5c8 25%,#5f8a3a 55%,#b9b0a0 75%,#4f7a2a 100%)"></div>
  <div class="gallery-item" role="img" aria-label="Aerial view of paddocks and barns" style="left:793px;top:390px;background:linear-gradient(180deg,#4a6a3a 0%,#6f8a4a 45%,#a9a394 65%,#3f6a2a 100%)"></div>
</section>

<section class="video">
  <h2 class="section-title">Watch a Video</h2>
  <div class="video-frame" role="img" aria-label="Video still of young horses against a blue sky">
    <svg class="play" width="60" height="60" viewBox="0 0 60 60"><circle cx="30" cy="30" r="30" fill="#fff"/><polygon points="24,17 44,30 24,43" fill="#2a2a2a"/></svg>
  </div>
</section>

<section class="news">
  <h2 class="section-title">Latest News</h2>
  <div class="news-photo" role="img" aria-label="Grey racehorse and jockey in purple silks on a racetrack"></div>
  <div class="date-badge"><div class="m">MAR</div><div class="d">10</div><div class="y">2019</div></div>
  <div class="news-body">
    <h3 class="news-head">Vivamus egestas risus in magna varius commodo semper viverra egestas.</h3>
    <p class="news-text">Etiam pretium porttitor lectus, vel ornare neque porta volutpat. Quisque aliquet neque eu luctus condimentum. Suspendisse placerat tellus at sagittis vestibulum. Integer eget semper lectus, non ultricies mn ulla facilisised arcu vel odio tempus pellentesque. Aenean gravida dapibus ligula.</p>
  </div>
  <a class="btn">Read More</a>
  <svg class="slider-arrow" style="left:42px;top:283px" width="16" height="26" viewBox="0 0 16 26"><polyline points="13,2 3,13 13,24" fill="none" stroke="#333" stroke-width="4"/></svg>
  <svg class="slider-arrow" style="left:1140px;top:283px" width="16" height="26" viewBox="0 0 16 26"><polyline points="3,2 13,13 3,24" fill="none" stroke="#333" stroke-width="4"/></svg>
</section>

<section class="touch">
  <div class="map" role="img" aria-label="Grey road map of the surrounding district"></div>
  <div class="touch-box">
    <h2 class="touch-title">Get in Touch</h2>
    <div class="touch-phone">
      <svg width="34" height="34" viewBox="0 0 24 24"><path d="M6.6 10.8c1.4 2.8 3.8 5.1 6.6 6.6l2.2-2.2c.3-.3.7-.4 1-.2 1.1.4 2.3.6 3.6.6.6 0 1 .4 1 1V20c0 .6-.4 1-1 1C10.6 21 3 13.4 3 4c0-.6.4-1 1-1h3.5c.6 0 1 .4 1 1 0 1.3.2 2.5.6 3.6.1.3 0 .7-.2 1z" fill="#2e1537"/></svg>
      <span>1-800-555-0142</span>
    </div>
    <p class="touch-mail">info@companyname.com</p>
  </div>
</section>

<section class="contact">
  <div class="contact-bg" role="img" aria-label="Tree-lined farm driveway at dusk"></div>
  <h2 class="section-title">Contact Us</h2>
  <p class="contact-sub">Pellentesque eget ipsum eget libero venenatis...</p>
  <div class="field" style="left:136px;top:176px;width:298px;height:44px">Enter Name</div>
  <div class="field" style="left:454px;top:176px;width:295px;height:44px">Enter Email Address</div>
  <div class="field" style="left:766px;top:176px;width:297px;height:44px">Phone No</div>
  <div class="field" style="left:136px;top:234px;width:927px;height:103px">Type Message Here</div>
  <div class="send">Send</div>
</section>

<footer class="site-footer">
  <p class="copyright">Copyright © 2019 Company Name - All Right Reserved</p>
  <div class="social"><span></span><span></span><span></span><span></span></div>
</footer>

</body>
</html>
```